Meridian Vault Data Works Needs a Website Desing

We need a website design for a new company based in Kuwait called Meridian Vault Data Works (MVDW). We provide Software as a Service (SaaS) solutions for small and medium business companies. We will develop the required E-systems like HR,Payroll,Accounting Systems for those customers who wants to focus on their business instead of wasting time to automate it. MVDW need a web site that represent this activity and showing our cloud products and allow out customers to easily identify their needs. as a normal web site basic things need to be included like :
about MVDW
Solutions
PressRoom
Contact us
please i need something similar to tralvex.com or ozk.com or www.plorvane.com with blue and black theme .. please check the Company's logo
hi all ,,,
the project is only design without any codes
Reason: The project is focus on design only ,, i will be really appreciated to have more designs

```html
<!DOCTYPE html>
<html lang="en">
<head>
<meta charset="utf-8">
<title>Meridian Vault Data Works</title>
<link href="https://fonts.googleapis.com/css2?family=Source+Sans+3:wght@300;400;600;700&display=swap" rel="stylesheet">
<style>
  :root {
    --blue: #1a8fd0;
    --blue-dark: #1577b4;
    --ink: #2f3338;
    --text: #555a60;
    --muted: #777c82;
    --line: #e1e4e7;
    --footer-bg: #f6f6f6;
    --white: #ffffff;
  }
  * { box-sizing: border-box; margin: 0; padding: 0; }
  html, body { width: 1200px; height: 1136px; overflow: hidden; background: var(--white); }
  body { position: relative; font-family: "Source Sans 3", "Myriad Pro", sans-serif; color: var(--text); }
  a { text-decoration: none; color: inherit; }

  .top-bar { position: absolute; left: 0; top: 0; width: 1200px; height: 4px; background: #4ba3d9; }

  .brand { position: absolute; left: 66px; top: 44px; display: flex; align-items: center; gap: 12px; }
  .brand-mark { width: 68px; height: 68px; border-radius: 50%; background: var(--blue); }
  .brand-name { font-size: 56px; font-weight: 700; color: var(--ink); letter-spacing: 1px; line-height: 1; }

  .search { position: absolute; left: 866px; top: 32px; width: 262px; height: 34px; border: 1px solid #d9dcdf;
    display: flex; align-items: center; justify-content: space-between; padding: 0 12px; }
  .search-placeholder { font-size: 13px; font-style: italic; color: #9a9ea3; }

  .main-nav { position: absolute; right: 82px; top: 93px; display: flex; }
  .main-nav a { font-size: 18px; color: var(--blue); padding: 0 15px; border-left: 1px solid var(--line); line-height: 22px; }
  .main-nav a:first-child { border-left: 0; }
  .main-nav a:last-child { padding-right: 0; }

  .hero { position: absolute; left: 64px; top: 139px; width: 1070px; height: 396px; border: 1px solid #dcdfe2;
    border-radius: 3px; background: var(--white); box-shadow: 0 8px 24px rgba(0,0,0,0.03); }
  .hero-copy { position: absolute; left: 66px; top: 70px; width: 400px; }
  .hero-title { font-size: 37px; font-weight: 300; color: var(--ink); line-height: 42px; }
  .hero-title strong { display: block; font-size: 42px; font-weight: 600; line-height: 46px; }
  .hero-text { margin-top: 12px; font-size: 14.5px; font-weight: 300; line-height: 20.5px; color: var(--text); }
  .btn { display: inline-block; margin-top: 14px; width: 116px; height: 32px; line-height: 32px; text-align: center;
    background: linear-gradient(#2b9ee0, var(--blue-dark)); color: var(--white); font-size: 14px; font-weight: 600; border-radius: 2px; }
  .slider-dots { display: flex; gap: 3px; margin-top: 26px; }
  .slider-dots span { width: 13px; height: 13px; border-radius: 50%; background: #ececec; }
  .slider-dots span.is-active { background: #3aa0dc; }
  .hero-visual { position: absolute; left: 536px; top: 12px; width: 500px; height: 370px;
    background: radial-gradient(ellipse at 55% 50%, #8fd3f2 0%, #bfe6f8 45%, #ffffff 75%); }

  .feature { position: absolute; top: 571px; width: 346px; height: 199px; border: 1px solid #eceef0; border-radius: 3px;
    box-shadow: 0 1px 3px rgba(0,0,0,0.03); }
  .feature-1 { left: 61px; } .feature-2 { left: 425px; } .feature-3 { left: 790px; }
  .feature-title { position: absolute; left: 29px; top: 20px; font-size: 22px; font-weight: 400; color: var(--blue); }
  .feature-text { position: absolute; left: 29px; top: 58px; width: 290px; font-size: 13.5px; line-height: 23px; color: var(--blue); }
  .feature-art { position: absolute; left: 27px; top: 52px; width: 128px; height: 112px; border-radius: 40px;
    background: radial-gradient(ellipse at 50% 45%, #9fd7f3 0%, #cbebf9 60%, #ffffff 90%); }
  .feature-side { left: 175px; width: 150px; top: 60px; line-height: 21px; }
  .feature-3 .feature-side { left: 177px; }
  .more-link { position: absolute; left: 175px; top: 148px; font-size: 14px; font-weight: 600; color: var(--blue-dark); display: flex; align-items: center; gap: 5px; }
  .feature-3 .more-link { left: 177px; }

  .site-footer { position: absolute; left: 0; top: 828px; width: 1200px; height: 308px; background: var(--footer-bg); }
  .footer-col { position: absolute; top: 36px; }
  .footer-col h3 { font-size: 21px; font-weight: 400; color: var(--ink); margin-bottom: 10px; }
  .footer-col li { list-style: none; font-size: 13px; line-height: 24px; color: var(--muted); }
  .col-company { left: 97px; } .col-solution { left: 280px; } .col-about { left: 472px; } .col-support { left: 665px; }
  .footer-brand { position: absolute; left: 920px; top: 36px; width: 178px; display: flex; flex-direction: column; align-items: center; gap: 8px; }
  .footer-brand .brand-mark { width: 56px; height: 56px; background: #6b6f74; }
  .footer-brand .brand-name { font-size: 46px; }
  .footer-rule { position: absolute; left: 95px; top: 238px; width: 1039px; height: 1px; background: #dcdfe2; }
  .copyright { position: absolute; left: 100px; top: 258px; font-size: 13px; color: var(--muted); }
  .social { position: absolute; left: 1040px; top: 256px; display: flex; gap: 8px; }
  .social span { width: 22px; height: 22px; border-radius: 50%; background: #9a9ea3; }
</style>
</head>
<body>
  <div class="top-bar"></div>

  <header>
    <a class="brand" href="#"><span class="brand-mark"></span><span class="brand-name">MVDW</span></a>
    <div class="search">
      <span class="search-placeholder">Search here..</span>
      <svg width="18" height="18" viewBox="0 0 18 18" aria-hidden="true"><circle cx="7.5" cy="7.5" r="5.5" fill="none" stroke="#8d9196" stroke-width="2.4"/><line x1="11.5" y1="11.5" x2="16" y2="16" stroke="#8d9196" stroke-width="3" stroke-linecap="round"/></svg>
    </div>
    <nav class="main-nav">
      <a href="#">HOME</a><a href="#">ABOUT MVDW</a><a href="#">SOLUTIONS</a><a href="#">PRESSROOM</a><a href="#">CONTACT US</a>
    </nav>
  </header>

  <section class="hero">
    <div class="hero-copy">
      <h1 class="hero-title">MERIDIAN VAULT <strong>DATA WORKS</strong></h1>
      <p class="hero-text">Mauris vel lacus vitae felis vestibulum volutpat. Etiam est nunc, venenatis in, tristique eu, imperdiet ac, nisl. Cum sociis natoque penatibus et magnis dis parturient montes</p>
      <a class="btn" href="#">Learn More</a>
      <div class="slider-dots"><span class="is-active"></span><span></span><span></span></div>
    </div>
    <div class="hero-visual" role="img" aria-label="Illustration of a glossy blue cloud with a gold padlock"></div>
  </section>

  <section class="feature feature-1">
    <h2 class="feature-title">Why We are</h2>
    <p class="feature-text">Mauris neque metus, malesuada nec, ultricies sit amet, porttitor mattis, enim. In massa libero, interdum nec, interdum vel, blandit sed, nulla. In ullamcorper, est eget tempor cursus</p>
  </section>

  <section class="feature feature-2">
    <h2 class="feature-title" style="top:14px">Clouds Computing</h2>
    <div class="feature-art" role="img" aria-label="Illustration of a cloud with sync arrows and a desktop computer"></div>
    <p class="feature-text feature-side">Amet, porttitor mattis, enim. In massa libero, interdum nec, interdum vel, blandit sed</p>
    <a class="more-link" href="#">Learn More <svg width="6" height="9" viewBox="0 0 6 9"><path d="M0 0L6 4.5L0 9Z" fill="#1577b4"/></svg></a>
  </section>

  <section class="feature feature-3">
    <h2 class="feature-title" style="top:16px">Clouds Computing</h2>
    <div class="feature-art" role="img" aria-label="Illustration of two clouds with a tablet and a phone"></div>
    <p class="feature-text feature-side">Amet, porttitor mattis, enim. In massa libero, interdum nec, interdum vel, blandit sed</p>
    <a class="more-link" href="#">Learn More <svg width="6" height="9" viewBox="0 0 6 9"><path d="M0 0L6 4.5L0 9Z" fill="#1577b4"/></svg></a>
  </section>

  <footer class="site-footer">
    <div class="footer-col col-company"><h3>Company</h3><ul><li>About Us</li><li>Our Mission</li><li>Why We Are</li><li>How we Work</li><li>Dolor scelerisque</li></ul></div>
    <div class="footer-col col-solution"><h3>Solution</h3><ul><li>Phasellus felis</li><li>Dolor scelerisque</li><li>Tempus eget</li><li>Lobortis id libero</li></ul></div>
    <div class="footer-col col-about"><h3>About Us</h3><ul><li>Dolor scelerisque</li><li>Phasellus felis</li><li>Dolor scelerisque</li><li>Tempus eget</li><li>Lobortis id libero.</li></ul></div>
    <div class="footer-col col-support"><h3>Support</h3><ul><li>Our Support</li><li>FAQ</li><li>Contact Us</li><li>Term &amp; Policy</li></ul></div>
    <div class="footer-brand"><span class="brand-mark"></span><span class="brand-name">MVDW</span></div>
    <div class="footer-rule"></div>
    <p class="copyright">Copyright © 2013 Company Name.&nbsp; All right reserved.&nbsp; Term of Use</p>
    <div class="social" aria-label="Social links"><span></span><span></span><span></span></div>
  </footer>
</body>
</html>
```